QVR business card

Need a business card for a company that provides instructional design and elearning development services. The website is here: http://quorvane.studio/

I'm attaching a current logo, as well as the old business card design. While I like to keep it clean, the old design is too simplistic for my liking. The only idea I want to reuse from the old design is placing industry jargon on the back of the card, just need a better way to present it. But if you have other ideas for the back--feel free to experiment.

Please use the colors complementary to the color we have on the website. Thank you!

```html
<!DOCTYPE html>
<html lang="en">
<head>
<meta charset="utf-8">
<title>QVR business card</title>
<link rel="stylesheet" href="https://fonts.googleapis.com/css2?family=Lato:wght@400;700&family=Montserrat:wght@700&family=Roboto+Condensed:wght@700&display=swap">
<style>
  :root{
    --teal:#17aea6;
    --teal-text:#1aa79e;
    --ink:#3a3a3a;
    --slate:#4d4e50;
    --card-dark:#222425;
    --paper:#ffffff;
    --backdrop:#ecebe8;
  }
  *{box-sizing:border-box;margin:0;padding:0}
  html,body{width:1138px;height:1200px;overflow:hidden}
  body{background:var(--backdrop);position:relative;font-family:"Lato",sans-serif}

  .card{position:absolute;left:234px;width:670px;height:383px;border-radius:12px;overflow:hidden;box-shadow:0 6px 14px rgba(0,0,0,.18)}

  /* Front */
  .card--front{top:198px;background:var(--paper)}
  .brand{position:absolute;left:40px;top:52px;display:flex;align-items:center;gap:14px}
  .brand__dot{width:22px;height:22px;border-radius:50%;background:var(--teal)}
  .brand__name{font-family:"Lato",sans-serif;font-weight:700;font-size:62px;letter-spacing:6px;color:var(--teal);line-height:1}
  .holder{position:absolute;left:38px;top:240px;font-size:21px;font-weight:700;color:var(--teal-text);letter-spacing:.2px}
  .contacts{position:absolute;left:38px;top:280px;list-style:none}
  .contacts li{display:flex;align-items:center;gap:9px;font-size:17.5px;color:var(--ink);height:23px}
  .contacts svg{width:17px;height:17px;flex:none}
  .band{position:absolute;left:0;bottom:0;width:100%;height:24px}

  /* Back */
  .card--back{top:617px;background:var(--card-dark)}
  .jargon{position:absolute;left:38px;width:596px;display:flex;justify-content:space-between;column-gap:16px;white-space:nowrap;font-family:"Montserrat",sans-serif;font-weight:700;font-size:33px;letter-spacing:1.5px;color:var(--teal);line-height:1}
  .jargon--1{top:24px}.jargon--2{top:72px}.jargon--3{top:120px}
  .jargon--4{top:230px;left:42px}.jargon--5{top:278px;left:42px}.jargon--6{top:326px;left:42px}
  .question{position:absolute;left:0;top:160px;width:100%;height:57px;display:flex;align-items:center;justify-content:space-between}
  .question__mark{width:22px;height:57px;background:var(--paper)}
  .question__text{flex:1;display:flex;justify-content:space-between;padding:0 18px;white-space:nowrap;font-family:"Roboto Condensed",sans-serif;font-weight:700;font-size:74px;letter-spacing:-4px;color:var(--paper);line-height:1}
</style>
</head>
<body>

<section class="card card--front" aria-label="Business card front">
  <div class="brand">
    <span class="brand__dot"></span>
    <span class="brand__name">QVR</span>
  </div>

  <p class="holder">Marlen Okafor</p>
  <ul class="contacts">
    <li>
      <svg viewBox="0 0 24 24" aria-hidden="true"><path fill="var(--teal)" d="M6.6 3.5l3 .4 1.2 4.4-2.2 1.6c1 2.4 2.8 4.3 5.2 5.4l1.6-2.2 4.3 1.2.4 3c-.3 1.5-1.6 2.4-3.1 2.3C9.9 19 5 14.1 4.3 6.6c-.1-1.5.8-2.8 2.3-3.1z"/></svg>
      555-014-2876
    </li>
    <li>
      <svg viewBox="0 0 24 24" aria-hidden="true"><rect x="2" y="5" width="20" height="14" fill="var(--teal)"/><path d="M2.5 5.5l9.5 8 9.5-8M2.5 18.5l7-6.5M21.5 18.5l-7-6.5" stroke="#fff" stroke-width="1.6" fill="none"/></svg>
      mokafor@quorvane.studio
    </li>
    <li>
      <svg viewBox="0 0 24 24" aria-hidden="true"><g fill="none" stroke="var(--teal)" stroke-width="1.7"><circle cx="12" cy="12" r="9.5"/><ellipse cx="12" cy="12" rx="4.2" ry="9.5"/><path d="M2.5 12h19M4 7h16M4 17h16"/></g></svg>
      www.quorvane.studio
    </li>
  </ul>

  <svg class="band" viewBox="0 0 670 24" preserveAspectRatio="none" aria-hidden="true">
    <rect width="670" height="24" fill="var(--slate)"/>
    <polygon points="0,0 492,0 468,24 0,24" fill="var(--teal)"/>
    <polygon points="492,0 500,0 476,24 468,24" fill="var(--paper)"/>
  </svg>
</section>

<section class="card card--back" aria-label="Business card back">
  <p class="jargon jargon--1"><span>MOBILE</span><span>LEARNING</span><span>SCORM</span></p>
  <p class="jargon jargon--2"><span>INSTRUCTIONAL</span><span>DESIGN</span><span>LMS</span></p>
  <p class="jargon jargon--3"><span>MOOCS</span><span>ELEARNING</span><span>HTML5</span></p>

  <div class="question">
    <span class="question__mark"></span>
    <p class="question__text"><span>HOW</span><span>CAN</span><span>WE</span><span>HELP?</span></p>
    <span class="question__mark"></span>
  </div>

  <p class="jargon jargon--4"><span>ADULT</span><span>LEARNING</span><span>THEORY</span></p>
  <p class="jargon jargon--5"><span>GAMIFICATION</span><span>CLASSROOM</span></p>
  <p class="jargon jargon--6"><span>XAPI</span><span>BLENDED</span><span>LEARNING</span></p>
</section>

</body>
</html>
```